Dental Practice Billboard Design

We are a newer dental practice in need of a simple but appealing billboard for our growing dental practice to attract new patients. The practice is owned by husband and wife dentists and is family friendly in a small town in Kentucky. We try to be very friendly and caring to our patients. Would prefer a blue background for the billboard and our tooth logo to be prominent. We are partial to the Patua One font used in the image below but please feel free to tweak it as you deem necessary. The shape of the uppercase D and lowercase g are why we like that font, so fonts with a similarly shaped “D” and “g” would work as well. Please include our phone number (555) 847-1390. Please see our website Harlowbrookdentistry.example for more info on the practice if needed. Thank you! Looking forward to seeing your creation.
Updates

The dimensions will be 12ft x 24ft (3.6576m x 7.3152m). Apologies for not including this in the original prompt. Thank you all for your submissions.

Industry/Entity Type

Dental

Font styles to use
Other font styles liked:
• Patua One

Colors
0054AA
0677BA
7BADD7
CADEEF
E8F1F8
0094D4
00A9DD
6FCCEA
C7EBF8
E9F6FB
00AB8E
00BBA5
67D7C9
C6EFE9
E9F9F6
59FF00
82FF00
B8FF75
E3FFCB
F4FFEA

Requirements
Must have
• Phone number, website, Logo, Practice name “Harlow Brook Dentistry”
Should not have
• A tagline or slogan

```html
<!DOCTYPE html>
<html lang="en">
<head>
<meta charset="utf-8">
<title>Harlow Brook Dentistry – Billboard</title>
<link href="https://fonts.googleapis.com/css2?family=Patua+One&family=Montserrat:wght@700&display=swap" rel="stylesheet">
<style>
  :root {
    --page-bg: #2b2f3a;
    --brand-blue: #0054aa;
    --brand-green: #16b21c;
    --white: #ffffff;
    --ink: #111111;
  }
  * { margin: 0; padding: 0; box-sizing: border-box; }
  html, body { width: 1200px; height: 835px; overflow: hidden; }
  body { background: var(--page-bg); position: relative; }

  .billboard {
    position: absolute;
    left: 40px;
    top: 137px;
    width: 1120px;
    height: 560px;
    background: var(--brand-blue);
    overflow: hidden;
    font-family: "Patua One", Georgia, serif;
    color: var(--white);
  }

  .identity {
    position: absolute;
    left: 0;
    top: 0;
    width: 100%;
    height: 420px;
    display: flex;
    align-items: center;
    justify-content: center;
    gap: 44px;
  }
  .brand-mark {
    flex: none;
    width: 190px;
    height: 190px;
    border-radius: 50%;
    background: var(--brand-green);
  }
  .practice-name {
    font-weight: 400;
    line-height: 1;
  }
  .practice-name .name-main {
    display: block;
    font-size: 150px;
  }
  .practice-name .name-sub {
    display: block;
    font-size: 68px;
    margin-top: 10px;
    margin-left: 4px;
  }

  .contact-bar {
    position: absolute;
    left: 0;
    bottom: 0;
    width: 100%;
    height: 110px;
    background: var(--white);
  }
  .phone-band {
    position: absolute;
    left: 0;
    bottom: 0;
    width: 550px;
    height: 140px;
    background: var(--brand-green);
    clip-path: polygon(0 0, 495px 0, 550px 100%, 0 100%);
    display: flex;
    align-items: center;
    padding-left: 56px;
  }
  .phone {
    font-family: "Montserrat", Arial, sans-serif;
    font-weight: 700;
    font-size: 56px;
    color: var(--white);
  }
  .website {
    position: absolute;
    right: 40px;
    top: 0;
    height: 100%;
    display: flex;
    align-items: center;
    gap: 14px;
    font-family: "Montserrat", Arial, sans-serif;
    font-weight: 700;
    font-size: 26px;
    color: var(--ink);
  }
  .website svg { flex: none; }
</style>
</head>
<body>
  <div class="billboard">
    <div class="identity">
      <div class="brand-mark"></div>
      <h1 class="practice-name">
        <span class="name-main">Harlow</span>
        <span class="name-sub">Brook Dentistry</span>
      </h1>
    </div>
    <div class="contact-bar">
      <div class="phone-band">
        <span class="phone">(555) 847-1390</span>
      </div>
      <div class="website">
        <svg width="36" height="36" viewBox="0 0 40 40" aria-hidden="true">
          <g fill="none" stroke="#16b21c" stroke-width="2.5">
            <circle cx="20" cy="20" r="17"/>
            <ellipse cx="20" cy="20" rx="8" ry="17"/>
            <line x1="3" y1="20" x2="37" y2="20"/>
            <line x1="20" y1="3" x2="20" y2="37"/>
            <path d="M6 11 H34 M6 29 H34"/>
          </g>
        </svg>
        <span>Harlowbrookdentistry.example</span>
      </div>
    </div>
  </div>
</body>
</html>
```